4th Generation Family Business Needs a New Card Design!

We are a family owned 4th Generation company. We are based in the Sydney, Australia area and we are desperately in need of a more modern and classy card. We are monumental masons who design, supply & erect lasting memorials throughout cemeteries in Sydney. Our customers are normally in a period of grieving. I have attached logo files that will need to be implemented on the card. Company was established 1935. Australian Owned and Operated. Card needs to be designed to PIXO.com specification.

Target Market(s)

Our target market is based upon people that a grieving for family members that have passed away. We also deal with alot of companies that own and operate cemeteries.

Industry/Entity Type

Business

Contact Information for Business Card

Simon Harcourt, Operations Manager, 0417293086, simon@harcourtmemorials.com.au
Lewis Harcourt, Director, 0491630572, lewis@harcourtmemorials.com.au
Phone # 02 9561 3048
Website: www.harcourtmemorials.com.au
Address: Suite 17, 8 Palfrey Lane, West Carlow, Sydney NSW 2156

Font styles to use
Serif
Decorative
Script

Requirements
Must have
• Would like to see the logo nicely implemented with a modern design. Embossed lettering would be a nice additive.

```html
<!DOCTYPE html>
<html lang="en">
<head>
<meta charset="utf-8">
<title>Harcourt Memorials – Business Card</title>
<link rel="stylesheet" href="https://fonts.googleapis.com/css2?family=Montserrat:wght@400;500;600;700&display=swap">
<style>
  :root {
    --backdrop: #2b2b2b;
    --card-black: #050505;
    --card-white: #ffffff;
    --gold: #f2b705;
    --ink: #111111;
    --soft-white: #f4f4f4;
  }
  * { box-sizing: border-box; margin: 0; padding: 0; }
  html, body {
    width: 1200px; height: 900px; overflow: hidden;
    background: var(--backdrop);
    font-family: "Montserrat", sans-serif;
  }
  .stage { position: relative; width: 1200px; height: 900px; }
  .card {
    position: absolute; left: 250px; width: 700px; height: 400px;
    border-radius: 26px; overflow: hidden;
    box-shadow: 0 14px 30px rgba(0,0,0,.45);
  }

  /* Front */
  .card-front { top: 40px; background: var(--card-black); color: var(--soft-white); }
  .front-brand {
    position: absolute; left: 0; right: 0; top: 95px;
    display: flex; flex-direction: column; align-items: center; gap: 22px;
  }
  .brand-square {
    width: 64px; height: 64px; border: 4px solid var(--soft-white);
  }
  .brand-name {
    font-weight: 600; font-size: 40px; letter-spacing: 2px;
    text-transform: uppercase; text-align: center; line-height: 1.15;
    color: var(--soft-white);
  }
  .brand-name small { display: block; font-size: 24px; letter-spacing: 6px; font-weight: 600; }
  .front-web {
    position: absolute; left: 0; right: 0; bottom: 62px;
    text-align: center; font-size: 19px; font-weight: 500; color: var(--soft-white);
  }
  .front-web .accent { color: var(--gold); font-weight: 600; }

  /* Back */
  .card-back { top: 470px; background: var(--card-black); }
  .back-light {
    position: absolute; left: 0; top: 0; bottom: 0; width: 370px;
    background: var(--card-white);
  }
  .back-brand {
    position: absolute; left: 44px; top: 52px;
    font-weight: 600; font-size: 30px; letter-spacing: 1.5px;
    text-transform: uppercase; line-height: 1.15; color: var(--ink);
  }
  .back-brand small { display: block; font-size: 18px; letter-spacing: 5px; font-weight: 600; }
  .divider-mark {
    position: absolute; left: 318px; top: 150px; width: 104px; height: 104px;
    background: var(--card-white); border: 5px solid var(--ink);
    outline: 3px solid var(--card-white);
  }
  .holder {
    position: absolute; right: 52px; top: 64px; text-align: right;
  }
  .holder-name { font-weight: 600; font-size: 30px; color: var(--gold); }
  .holder-role { font-size: 14px; color: var(--soft-white); margin-top: 2px; }
  .holder-tab {
    position: absolute; right: 0; top: 64px; width: 30px; height: 38px;
    background: var(--card-white);
  }
  .contact {
    position: absolute; left: 44px; bottom: 38px;
    font-size: 14px; color: var(--ink); line-height: 1.45;
  }
  .contact-address { margin-bottom: 6px; }
  .contact-list { list-style: none; }
  .contact-list li { display: flex; align-items: center; gap: 10px; }
  .contact-list svg { width: 13px; height: 13px; flex: none; }
  .contact-list .accent { color: var(--gold); font-weight: 600; }
</style>
</head>
<body>
<main class="stage">

  <section class="card card-front" aria-label="Business card front">
    <div class="front-brand">
      <div class="brand-square"></div>
      <div class="brand-name">Harcourt<small>Memorials</small></div>
    </div>
    <p class="front-web">www.<span class="accent">harcourtmemorials</span>.com.au</p>
  </section>

  <section class="card card-back" aria-label="Business card back">
    <div class="back-light"></div>
    <div class="back-brand">Harcourt<small>Memorials</small></div>
    <div class="divider-mark"></div>

    <div class="holder">
      <p class="holder-name">Lewis Harcourt</p>
      <p class="holder-role">Director</p>
    </div>
    <div class="holder-tab"></div>

    <div class="contact">
      <p class="contact-address">Suite 17, 8 Palfrey Lane<br>West Carlow, Sydney NSW 2156</p>
      <ul class="contact-list">
        <li>
          <svg viewBox="0 0 12 12"><rect x="3" y="0.5" width="6" height="11" rx="1.2" fill="none" stroke="var(--gold)" stroke-width="1.4"/><circle cx="6" cy="9.4" r=".7" fill="var(--gold)"/></svg>
          0491630572
        </li>
        <li>
          <svg viewBox="0 0 12 12"><path d="M2.5 1 L4.6 1 L5.4 3.6 L4.1 4.6 Q5.2 7 7.4 8 L8.4 6.7 L11 7.5 L11 9.6 Q10.6 11 9 11 Q1 10.2 1 2.6 Q1 1 2.5 1 Z" fill="var(--gold)"/></svg>
          02 9561 3048
        </li>
        <li>
          <svg viewBox="0 0 12 12"><rect x="0.8" y="2.2" width="10.4" height="7.6" rx="1" fill="none" stroke="var(--gold)" stroke-width="1.3"/><path d="M1 2.8 L6 6.6 L11 2.8" fill="none" stroke="var(--gold)" stroke-width="1.3"/></svg>
          lewis@harcourtmemorials.com.au
        </li>
        <li>
          <svg viewBox="0 0 12 12"><circle cx="6" cy="6" r="5" fill="none" stroke="var(--gold)" stroke-width="1.3"/><ellipse cx="6" cy="6" rx="2.2" ry="5" fill="none" stroke="var(--gold)" stroke-width="1"/><path d="M1 6 H11" stroke="var(--gold)" stroke-width="1"/></svg>
          <span>www.<span class="accent">harcourtmemorials</span>.com.au</span>
        </li>
      </ul>
    </div>
  </section>

</main>
</body>
</html>
```